Billboard design 8x3M RAVU (Spanish company)

We´re located in the south of Spain. We run a local telecom company.
We sell Fiber optic, and mobile phone lines mainly.
The billboard will have to be in Spanish, I would like the price to be something you spot on first sight when passing by in the car.
Our company color is blue, like in our logo which I will add. I will also add a example from what we currently have.
The new offer should be:
1000 megas + 100Gigas movil con llamadas ilimitadas. (meaning 1000Mb fiber optic speed and 100Gb data and unlimited calls for 1 mobile line)
Our details are: phone line 958 47 6620
Website: ra-vu.es

```html
<!DOCTYPE html>
<html lang="es">
<head>
<meta charset="utf-8">
<title>RAVU – Valla 8x3</title>
<link href="https://fonts.googleapis.com/css2?family=Anton&family=Russo+One&family=Roboto:wght@400;700&family=Montserrat:wght@400;700&display=swap" rel="stylesheet">
<style>
  :root {
    --blue-deep: #04263d;
    --blue-mid: #0a5c8c;
    --blue-bright: #0f8fcf;
    --blue-text: #0d5d97;
    --sky: #8fd3f4;
    --gold: #e2a92c;
    --teal: #5f9a86;
    --white: #ffffff;
    --ink: #0c1b26;
    --page: #ffffff;
  }
  * { margin: 0; padding: 0; box-sizing: border-box; }
  html, body { width: 1067px; height: 1200px; overflow: hidden; background: var(--page); }

  .billboard {
    position: absolute; left: 33px; top: 430px;
    width: 1000px; height: 339px;
    overflow: hidden;
    background: linear-gradient(90deg, var(--blue-mid) 40%, var(--blue-bright) 75%);
  }
  .billboard__shapes { position: absolute; inset: 0; width: 100%; height: 100%; }

  .accent-bar { position: absolute; height: 6px; left: 0;
    background: linear-gradient(90deg, var(--gold) 60%, rgba(226,169,44,0)); }
  .accent-bar--1 { top: 1px; width: 99px; }
  .accent-bar--2 { top: 15px; width: 118px; }
  .accent-bar--3 { top: 29px; width: 144px; }
  .accent-bar--right { top: 0; left: 782px; width: 218px; height: 14px;
    background: linear-gradient(90deg, rgba(226,169,44,0.3), var(--gold) 40%); }

  .slogan {
    position: absolute; left: 23px; top: 149px;
    font-family: "Russo One", sans-serif; font-size: 23px; line-height: 25px;
    color: var(--sky); letter-spacing: 1px; font-style: italic;
    transform: skewX(-10deg); transform-origin: left;
  }

  .offer { position: absolute; right: 405px; top: 52px; text-align: right;
    font-family: "Anton", sans-serif; color: var(--white);
    text-shadow: 2px 2px 0 var(--ink); line-height: 1; }
  .offer__speed { font-size: 66px; letter-spacing: -1px; }
  .offer__data { font-size: 50px; margin-top: 4px; }
  .offer__calls { font-size: 21px; margin-top: 4px; letter-spacing: 0.5px; }
  .offer__price { font-size: 44px; margin-top: 8px; }

  .contact-band {
    position: absolute; left: 0; top: 284px; width: 623px; height: 47px;
    background: linear-gradient(90deg, var(--gold) 45%, var(--teal));
  }
  .contact-band__phone { position: absolute; left: 0; width: 348px; top: 3px; text-align: center;
    font-family: "Roboto", sans-serif; font-weight: 700; font-size: 23px; color: var(--blue-text); }
  .contact-band__web { position: absolute; left: 0; width: 348px; top: 26px; text-align: center;
    font-family: "Roboto", sans-serif; font-size: 17px; color: var(--blue-text); }

  .brand { position: absolute; left: 737px; top: 282px; color: var(--white); }
  .brand__name { font-family: "Anton", sans-serif; font-size: 32px; line-height: 36px; letter-spacing: 2px; }
  .brand__services { font-family: "Montserrat", sans-serif; font-size: 11px; margin-top: 2px; white-space: nowrap; }
  .brand__services b { font-weight: 700; }

  .contact-side { position: absolute; left: 878px; top: 298px; width: 96px; text-align: right;
    font-family: "Anton", sans-serif; line-height: 1.05; }
  .contact-side__phone { color: var(--gold); font-size: 19px; }
  .contact-side__web { color: var(--white); font-size: 14px; }
</style>
</head>
<body>
  <section class="billboard" aria-label="Valla publicitaria RAVU">
    <svg class="billboard__shapes" viewBox="0 0 1000 339" preserveAspectRatio="none">
      <defs>
        <linearGradient id="darkPanel" x1="0" y1="0" x2="1" y2="0">
          <stop offset="0" stop-color="#0a4e78"/>
          <stop offset="1" stop-color="#03223a"/>
        </linearGradient>
        <linearGradient id="photoTone" x1="0" y1="0" x2="1" y2="1">
          <stop offset="0" stop-color="#6f8fa6"/>
          <stop offset="0.5" stop-color="#3f6f92"/>
          <stop offset="1" stop-color="#1d4a6e"/>
        </linearGradient>
      </defs>
      <path d="M0 0 H298 C310 120 240 250 180 339 H0 Z" fill="url(#darkPanel)"/>
      <path d="M297 0 C310 90 300 140 288 160" fill="none" stroke="#ffffff" stroke-width="1.5"/>
      <path d="M746 0 H1000 V339 H623 C600 240 630 80 746 0 Z" fill="url(#photoTone)" role="img" aria-label="Foto de una familia mirando juntos una tableta en la cocina"/>
      <rect x="0" y="331" width="623" height="8" fill="#0a6ea6"/>
    </svg>

    <div class="accent-bar accent-bar--1"></div>
    <div class="accent-bar accent-bar--2"></div>
    <div class="accent-bar accent-bar--3"></div>
    <div class="accent-bar accent-bar--right"></div>

    <p class="slogan">TU FIBRA + MÓVIL<br>AL MEJOR PRECIO</p>

    <div class="offer">
      <p class="offer__speed">1000 Mb</p>
      <p class="offer__data">+100Gb</p>
      <p class="offer__calls">+ LLAMADAS ILIMITADAS</p>
      <p class="offer__price">por 18.45€</p>
    </div>

    <div class="contact-band">
      <p class="contact-band__phone">958 47 6620</p>
      <p class="contact-band__web">www.ra-vu.es</p>
    </div>

    <div class="brand">
      <p class="brand__name">RAVU</p>
      <p class="brand__services">Wifi | Fibra | <b>Mobil | Tv</b></p>
    </div>

    <div class="contact-side">
      <p class="contact-side__phone">958 47 6620</p>
      <p class="contact-side__web">WWW.RA-VU.ES</p>
    </div>
  </section>
</body>
</html>
```